Brisk Coatings business card for residential and commercial painting

A clean, professional design. Easy to read
Eye catching and elegant
Front could have some color variations
On the back of card I would like all black with signature logo

*Attached is my current business card and the items I want displayed

Contact Information for Business Card

Email, phone number, website, and owner name

Font styles to use
Serif

Requirements
Must have
• My logo with cool design and perhaps some paint splatter

```html
<!DOCTYPE html>
<html lang="en">
<head>
<meta charset="utf-8">
<title>Brisk Coatings – Business Card</title>
<link rel="stylesheet" href="https://fonts.googleapis.com/css2?family=Oswald:wght@400;500&family=Questrial&display=swap">
<style>
  :root {
    --brand-blue: #1172bd;
    --paint-dark: #38383a;
    --ink: #2e2e30;
    --rule: #9a9a9a;
    --card: #ffffff;
    --backdrop: #a9a9a9;
  }
  * { margin: 0; padding: 0; box-sizing: border-box; }
  html, body { width: 1200px; height: 1200px; overflow: hidden; }
  body { background: var(--backdrop); position: relative; font-family: "Questrial", sans-serif; }

  .card {
    position: absolute;
    top: 303px;
    width: 368px;
    height: 594px;
    background: var(--card);
    overflow: hidden;
    box-shadow: 3px 4px 6px rgba(0,0,0,0.45);
  }
  .card--front { left: 201px; }
  .card--back { left: 599px; width: 364px; }

  /* Front */
  .paint-band { position: absolute; inset: 0; }
  .brush-art {
    position: absolute;
    left: 11px; top: 0;
    width: 124px; height: 498px;
    border-radius: 0 0 20px 20px;
    background: linear-gradient(180deg, var(--brand-blue) 0%, var(--brand-blue) 56%, var(--paint-dark) 60%, var(--paint-dark) 100%);
  }
  .price-label {
    position: absolute;
    left: 155px; top: 136px;
    font-family: "Oswald", sans-serif;
    font-weight: 400;
    font-size: 29px;
    color: var(--brand-blue);
    letter-spacing: -0.5px;
  }

  /* Back */
  .wordmark {
    position: absolute;
    left: 0; right: 0; top: 136px;
    display: flex; align-items: center; justify-content: center; gap: 10px;
  }
  .wordmark__mark { width: 12px; height: 12px; background: var(--brand-blue); }
  .wordmark__name {
    font-family: "Oswald", sans-serif;
    font-weight: 500;
    font-size: 40px;
    line-height: 1;
    color: var(--paint-dark);
    text-transform: uppercase;
  }
  .owner {
    position: absolute; left: 0; right: 0; top: 383px;
    text-align: center;
  }
  .owner__name {
    font-family: "Oswald", sans-serif;
    font-weight: 400;
    font-size: 33px;
    line-height: 1;
    color: var(--brand-blue);
    letter-spacing: -0.5px;
  }
  .owner__title { font-size: 16.5px; color: var(--ink); margin-top: 2px; }

  .contact-icons {
    position: absolute; left: 0; right: 0; top: 449px;
    display: flex; justify-content: center; align-items: center; gap: 4px;
  }
  .contact-icons__rule { width: 52px; height: 1px; background: var(--rule); margin: 0 4px; }
  .contact-icons svg { width: 25px; height: 25px; display: block; }

  .contact-list {
    position: absolute; left: 0; right: 0; top: 481px;
    list-style: none; text-align: center;
    font-size: 16.5px; line-height: 21.5px; color: var(--ink);
  }
  .contact-list .accent { color: var(--brand-blue); }
</style>
</head>
<body>

  <section class="card card--front">
    <svg class="paint-band" viewBox="0 0 368 594" aria-hidden="true">
      <path d="M0 422 C40 430 90 432 135 440 C150 437 165 436 200 435 C260 434 320 436 368 438 L368 594 L0 594 Z" fill="var(--paint-dark)"/>
    </svg>
    <div class="brush-art" role="img" aria-label="Large paintbrush with blue handle dripping dark paint"></div>
    <p class="price-label">Price:</p>
  </section>

  <section class="card card--back">
    <div class="wordmark">
      <span class="wordmark__mark"></span>
      <span class="wordmark__name">Brisk Coatings</span>
    </div>

    <div class="owner">
      <h1 class="owner__name">Rafael "Raf"</h1>
      <p class="owner__title">Owner-Licensed &amp; Insured</p>
    </div>

    <div class="contact-icons">
      <span class="contact-icons__rule"></span>
      <svg viewBox="0 0 25 25" aria-label="Phone">
        <rect width="25" height="25" rx="3" fill="var(--brand-blue)"/>
        <path d="M6 10 Q12.5 5 19 10 L17 12 L15 10.5 L10 10.5 L8 12 Z" fill="#fff"/>
        <rect x="8" y="12" width="9" height="6" rx="1" fill="#fff"/>
      </svg>
      <svg viewBox="0 0 25 25" aria-label="Email">
        <rect width="25" height="25" rx="3" fill="var(--brand-blue)"/>
        <rect x="6" y="8" width="13" height="9" fill="none" stroke="#fff" stroke-width="1.3"/>
        <path d="M6 8 L12.5 13 L19 8 M6 17 L10.5 12.5 M19 17 L14.5 12.5" fill="none" stroke="#fff" stroke-width="1.1"/>
      </svg>
      <svg viewBox="0 0 25 25" aria-label="Website">
        <rect width="25" height="25" rx="3" fill="var(--brand-blue)"/>
        <circle cx="12.5" cy="12.5" r="7" fill="#fff"/>
        <circle cx="12.5" cy="12.5" r="4.5" fill="none" stroke="var(--brand-blue)" stroke-width="1"/>
      </svg>
      <span class="contact-icons__rule"></span>
    </div>

    <ul class="contact-list">
      <li>555.014.2290</li>
      <li>briskcoatingstn@mail.com</li>
      <li>www.<span class="accent">briskcoatingstn</span>.com</li>
    </ul>
  </section>

</body>
</html>
```